Website creation for audiovisual activities

I want a website for my director of photography activity. It's primarily composed of screenshots in gallery format, followed by detailed pages for each production.

Here's my current website:
www.lionelbaquet.com
I'd like a more modern and streamlined design, and for the site to be responsive on phones and computers. I also want to be able to easily add photos and text to it later.

Target Market(s)

productions society, directors and producers.

Industry/Entity Type

Audiovisual / TV

Coding

Coded - Design and coding required

Number of Pages Required

5+ page

Font styles to use
Sans Serif

Colors
0054AA
0677BA
7BADD7
CADEEF
E8F1F8
0094D4
00A9DD
6FCCEA
C7EBF8
E9F6FB
00AB8E
00BBA5
67D7C9
C6EFE9
E9F9F6
6B429C
8869AF
B7A5CE
E3DAEB
F3F0F8

Requirements
Must have
• a modern look with a photo gallery on the homepage
Nice to have
• a light background with large, dynamic images
Should not have
• a dark background and an overly classic look

```html
<!DOCTYPE html>
<html lang="fr">
<head>
<meta charset="utf-8">
<title>Julien Marvaud — Directeur de la Photographie</title>
<link href="https://fonts.googleapis.com/css2?family=Poppins:wght@300;400;500;600;700&display=swap" rel="stylesheet">
<style>
:root{
  --blue:#0054AA;--blue2:#0677BA;--blue-pale:#CADEEF;--blue-mist:#E8F1F8;
  --cyan:#00A9DD;--cyan2:#0094D4;
  --teal:#00AB8E;--teal2:#00BBA5;
  --purple:#6B429C;--purple2:#8869AF;--purple-pale:#B7A5CE;
  --navy:#16338A;--ink:#2b2f3a;--grey:#8a8f99;--white:#fff;
}
*{margin:0;padding:0;box-sizing:border-box}
html,body{width:1200px;height:2882px;overflow:hidden}
body{font-family:'Poppins',sans-serif;color:var(--ink);background:var(--white);position:relative}
a{color:inherit;text-decoration:none}
.abs{position:absolute}

/* hero */
.hero{position:absolute;left:0;top:0;width:1200px;height:562px;overflow:hidden}
.hero-media{position:absolute;inset:0;background:
  radial-gradient(ellipse at 75% 40%,#6a5a8e 0%,transparent 55%),
  radial-gradient(ellipse at 20% 70%,#3a3a6e 0%,transparent 60%),
  linear-gradient(160deg,#2c2350 0%,#4a3f78 45%,#2a2a55 100%)}
.hero-shade{position:absolute;inset:0;background:linear-gradient(180deg,rgba(22,30,90,.55) 0%,rgba(40,30,90,.25) 40%,rgba(30,30,70,.45) 100%)}
.nav{position:absolute;left:60px;top:17px;width:1080px;height:40px;display:flex;align-items:center}
.brand{color:#d9dcf0;line-height:1}
.brand-name{font-size:17px;font-weight:300;letter-spacing:.3px;display:block}
.brand-role{font-size:11px;font-weight:600;color:var(--purple-pale);display:block;margin-top:3px;padding-left:24px}
.nav-links{position:absolute;top:0;height:40px;display:flex;align-items:center;font-size:14.5px;color:#fff}
.nav-links a{position:absolute;white-space:nowrap}
.nav-links a.active{font-weight:600;text-decoration:underline;text-underline-offset:4px}
.btn-login{position:absolute;left:832px;top:0;width:100px;height:40px;border:1.5px solid #fff;border-radius:20px;color:#fff;font-size:14px;display:flex;align-items:center;justify-content:center}
.btn-start{position:absolute;left:943px;top:0;width:137px;height:40px;border-radius:20px;background:var(--purple);color:#fff;font-size:14px;display:flex;align-items:center;justify-content:center}
.hero-kicker{position:absolute;top:187px;width:1200px;text-align:center;font-size:13px;color:#8fb6e6;letter-spacing:.3px}
.hero-title{position:absolute;top:212px;width:1200px;text-align:center;font-size:49px;font-weight:600;color:#fff}
.hero-title span{color:var(--cyan)}
.hero-text{position:absolute;top:300px;left:250px;width:700px;text-align:center;font-size:21.5px;line-height:33px;color:#fff;font-weight:400}
.btn{display:flex;align-items:center;justify-content:center;gap:8px;border-radius:22px;font-weight:500;white-space:nowrap}
.btn-primary{background:var(--purple);color:#fff}
.btn-ghost{border:1.5px solid #fff;color:#fff}

/* gallery */
.gallery{position:absolute;left:0;top:562px;width:1200px;height:1031px;background:
  radial-gradient(ellipse at 85% 15%,#dbe6f3 0%,transparent 55%),
  radial-gradient(ellipse at 10% 90%,#e4e8ef 0%,transparent 60%),
  linear-gradient(180deg,#d9e3ee 0%,#e4eaf2 60%,#eef1f5 100%)}
.kicker{font-size:19px;color:var(--teal);letter-spacing:.5px}
.section-title{font-size:31px;font-weight:600;color:var(--blue)}
.see-all{font-size:20px;color:var(--blue2);display:flex;align-items:center;gap:10px}
.card{position:absolute;width:525px}
.card-media{height:306px;border-radius:12px;position:relative;overflow:hidden;box-shadow:0 4px 14px rgba(0,0,0,.15)}
.tag{position:absolute;left:15px;top:15px;height:28px;padding:0 22px;border-radius:14px;color:#fff;font-size:14.5px;display:flex;align-items:center}
.tag-purple{background:var(--purple)}
.tag-teal{background:var(--teal)}
.card-link{position:absolute;right:20px;top:20px;width:38px;height:38px;border-radius:50%;background:rgba(40,40,50,.75);display:flex;align-items:center;justify-content:center}
.card-title{margin-top:10px;font-size:20px;font-weight:600;color:var(--blue)}
.card-meta{margin-top:2px;font-size:13px;color:var(--grey)}

/* approach */
.approach{position:absolute;left:0;top:1593px;width:1200px;height:587px;background:var(--blue-mist)}
.approach-media{position:absolute;left:73px;top:49px;width:500px;height:496px;border-radius:12px;background:radial-gradient(ellipse at 45% 40%,#4a4a4e 0%,#2a2a2d 60%,#1d1d20 100%);box-shadow:0 6px 18px rgba(0,0,0,.25)}
.approach-body{position:absolute;left:600px;top:52px;width:560px}
.approach-body p{font-size:21.5px;line-height:36.7px;color:#333}

/* cta */
.cta{position:absolute;left:0;top:2180px;width:1200px;height:390px;background:
  radial-gradient(ellipse at 30% 80%,#c9cfd8 0%,transparent 55%),
  radial-gradient(ellipse at 80% 30%,#d6dce6 0%,transparent 60%),
  linear-gradient(180deg,#dfe5ee 0%,#d4dae4 100%);text-align:center}
.cta p{font-size:21.5px;line-height:37px;color:#333}

/* footer */
.footer{position:absolute;left:0;top:2570px;width:1200px;height:312px;background:var(--navy);color:#fff}
.rule{position:absolute;left:60px;width:1080px;height:1px;background:rgba(255,255,255,.3)}
.footer-brand .brand-name{font-size:22px;color:#c8cde8}
.footer-brand .brand-role{font-size:16px;color:#c8cde8;padding-left:30px;margin-top:4px}
.footer-desc{font-size:18px;line-height:28px;color:#d8dcf0}
.footer-head{font-size:18px;font-weight:600}
.footer-list a,.footer-list span{position:absolute;font-size:14.5px;white-space:nowrap}
.footer-list a.u{text-decoration:underline;text-underline-offset:3px}
.copyright{font-size:11.5px;color:#d8dcf0}
.social{position:absolute;top:2842px;width:29px;height:29px;border:1.5px solid #fff;border-radius:5px}
</style>
</head>
<body>

<header class="hero">
  <div class="hero-media" role="img" aria-label="Photo d'un opérateur en studio devant une caméra, une console de mixage et un ordinateur portable"></div>
  <div class="hero-shade"></div>
  <nav class="nav">
    <a class="brand" href="#"><span class="brand-name">JULIEN MARVAUD</span><span class="brand-role">Directeur Photo</span></a>
    <div class="nav-links">
      <a class="active" href="#" style="left:185px">Présentation</a>
      <a href="#" style="left:332px">Magazine</a>
      <a href="#" style="left:453px">Émission</a>
      <a href="#" style="left:568px">Événement</a>
      <a href="#" style="left:702px">Conférence</a>
    </div>
    <a class="btn-login" href="#">Login</a>
    <a class="btn-start" href="#">Get Started</a>
  </nav>
  <div class="hero-kicker">DIRECTEUR DE LA PHOTOGRAPHIE · PARIS</div>
  <h1 class="hero-title">Julien <span>Marvaud</span></h1>
  <p class="hero-text">Capturer l'instant, révéler la lumière. Une vision photographique au service des plus grandes productions audiovisuelles françaises.</p>
  <a class="btn btn-primary abs" href="#" style="left:380px;top:423px;width:213px;height:40px;font-size:14.5px">Voir less Production
    <svg width="18" height="12" viewBox="0 0 18 12"><path d="M1 6h15M11 1l5 5-5 5" fill="none" stroke="#fff" stroke-width="1.6"/></svg></a>
  <a class="btn btn-ghost abs" href="#" style="left:605px;top:423px;width:177px;height:40px;font-size:14.5px">
    <svg width="11" height="12" viewBox="0 0 11 12"><path d="M1 1l9 5-9 5z" fill="none" stroke="#fff" stroke-width="1.3"/></svg>Mon Parcours</a>
</header>

<section class="gallery">
  <div class="kicker abs" style="left:60px;top:78px">SELECTION</div>
  <h2 class="section-title abs" style="left:60px;top:107px">Productios Recentes</h2>
  <a class="see-all abs" href="#" style="right:60px;top:115px">Voir toutes les productions
    <svg width="20" height="14" viewBox="0 0 20 14"><path d="M1 7h17M12 1l6 6-6 6" fill="none" stroke="#0677BA" stroke-width="1.7"/></svg></a>

  <article class="card" style="left:60px;top:180px">
    <div class="card-media" role="img" aria-label="Photo d'une DJ aux platines vinyles" style="background:linear-gradient(135deg,#3a3530 0%,#2a2a2e 45%,#5c7a94 75%,#1e1e22 100%)">
      <span class="tag tag-purple">Emission Live</span>
      <span class="card-link"><svg width="16" height="16" viewBox="0 0 16 16"><path d="M3 13L13 3M5 3h8v8" fill="none" stroke="#fff" stroke-width="1.8"/></svg></span>
    </div>
    <h3 class="card-title">Productios Recentes</h3>
    <div class="card-meta">Canal Agora . 2025</div>
  </article>

  <article class="card" style="left:615px;top:180px">
    <div class="card-media" role="img" aria-label="Photo d'un photographe tenant un appareil argentique" style="background:radial-gradient(ellipse at 45% 45%,#6b5a52 0%,#2a2624 45%,#0a0a0c 80%)">
      <span class="tag tag-teal">Documentaire</span>
      <span class="card-link"><svg width="16" height="16" viewBox="0 0 16 16"><path d="M3 13L13 3M5 3h8v8" fill="none" stroke="#fff" stroke-width="1.8"/></svg></span>
    </div>
    <h3 class="card-title">Horizons Lointains</h3>
    <div class="card-meta">Canal Agora . 2025</div>
  </article>

  <article class="card" style="left:60px;top:575px">
    <div class="card-media" role="img" aria-label="Photo d'une foule de concert sous des projecteurs bleus" style="background:radial-gradient(ellipse at 40% 30%,#7fc6f0 0%,#1b6fc4 30%,#0a2a66 60%,#050a18 100%)">
      <span class="tag tag-teal">Documentaire</span>
      <span class="card-link"><svg width="16" height="16" viewBox="0 0 16 16"><path d="M3 13L13 3M5 3h8v8" fill="none" stroke="#fff" stroke-width="1.8"/></svg></span>
    </div>
    <h3 class="card-title">Maman Chanteuse</h3>
    <div class="card-meta">Canal Trois . 2025</div>
  </article>

  <article class="card" style="left:615px;top:575px">
    <div class="card-media" role="img" aria-label="Photo d'une caméra de plateau télévisé sous éclairage bleu et violet" style="background:linear-gradient(160deg,#3a3a8a 0%,#5a4ab0 30%,#1e2a66 60%,#0c1430 100%)">
      <span class="tag tag-purple">Serie Tv</span>
      <span class="card-link"><svg width="16" height="16" viewBox="0 0 16 16"><path d="M3 13L13 3M5 3h8v8" fill="none" stroke="#fff" stroke-width="1.8"/></svg></span>
    </div>
    <h3 class="card-title">La Ligne de Fuite</h3>
    <div class="card-meta">Canal Deux . 2025</div>
  </article>
</section>

<section class="approach">
  <div class="approach-media" role="img" aria-label="Portrait d'une opératrice appuyée sur une caméra montée sur trépied"></div>
  <div class="approach-body">
    <div class="kicker">MON APPROCHE</div>
    <h2 class="section-title" style="margin-top:4px;margin-bottom:12px">L'image au service de l'histoire</h2>
    <p>Depuis plus de 15 ans, je mets ma vision photographique au service des productions télévisuelles, documentaires et cinématographiques. Mon approche repose sur une écoute attentive du réalisateur et une maîtrise technique au service de l'émotion.<br>Chaque projet est une nouvelle conversation entre la lumière et la narration, entre la technique et la sensibilité artistique.</p>
  </div>
  <a class="btn btn-primary abs" href="#" style="left:600px;top:500px;width:168px;height:40px;font-size:14px">En Savoir Plus
    <svg width="18" height="12" viewBox="0 0 18 12"><path d="M1 6h15M11 1l5 5-5 5" fill="none" stroke="#fff" stroke-width="1.6"/></svg></a>
</section>

<section class="cta" role="region" aria-label="Contact">
  <div class="kicker" style="position:absolute;top:72px;width:1200px;letter-spacing:0">Travaillons ensemble</div>
  <h2 class="section-title" style="position:absolute;top:110px;width:1200px">Vous avez un projet?</h2>
  <p style="position:absolute;top:165px;left:180px;width:840px">Que vous soyez réalisateur, producteur ou directeur de production, je serai ravi d'étudier votre projet et d'y apporter ma vision.</p>
  <a class="btn btn-primary abs" href="#" style="left:508px;top:270px;width:184px;height:48px;font-size:15px;border-radius:24px">Me Contacter
    <svg width="18" height="12" viewBox="0 0 18 12"><path d="M1 6h15M11 1l5 5-5 5" fill="none" stroke="#fff" stroke-width="1.6"/></svg></a>
</section>

<footer class="footer">
  <div class="rule" style="top:27px"></div>
  <div class="brand footer-brand abs" style="left:83px;top:66px"><span class="brand-name">JULIEN MARVAUD</span><span class="brand-role">Directeur Photo</span></div>
  <p class="footer-desc abs" style="left:83px;top:130px;width:400px">Directeur de la Photographie et Chef Opérateur pour la télévision, le cinéma et les productions audiovisuelles depuis plus de 15 ans.</p>
  <div class="footer-head abs" style="left:593px;top:58px">Naviguer</div>
  <div class="footer-list">
    <a class="u" href="#" style="left:593px;top:102px;font-weight:600">Présentation</a>
    <a class="u" href="#" style="left:593px;top:135px">Magazine</a>
    <a class="u" href="#" style="left:593px;top:168px">Événement</a>
    <a href="#" style="left:593px;top:201px">Conférence</a>
    <span style="left:895px;top:102px">0611223344</span>
    <span style="left:895px;top:135px">contact@julienmarvaud.fr</span>
  </div>
  <div class="footer-head abs" style="left:895px;top:58px">Connect</div>
  <div class="rule" style="top:252px"></div>
  <div class="copyright abs" style="left:0;width:1200px;text-align:center;top:274px">© 2026 Julien Marvaud. All rights reserved.</div>
</footer>
<a class="social" href="#" aria-label="Réseau professionnel" style="left:1000px"></a>
<a class="social" href="#" aria-label="Réseau social" style="left:1042px"></a>
<a class="social" href="#" aria-label="Réseau photo" style="left:1083px"></a>

</body>
</html>
```